Dunmore Roofing

Want a professional looking business card

Industry/Entity Type

Business

Contact Information for Business Card

Paul Dunmore ( Owner) paul@dunmoreroofing-example.com, www.dunmoreroofing-example.com, Adress: 4172 Township road 43 Bramhollow,ON K9X4T2

```html
<!DOCTYPE html>
<html lang="en">
<head>
<meta charset="utf-8">
<title>Dunmore Roofing – Business Card</title>
<link rel="stylesheet" href="https://fonts.googleapis.com/css2?family=Source+Sans+3:wght@400;600;700&display=swap">
<style>
  :root {
    --backdrop: #3a3532;
    --card: #151517;
    --brand-blue: #2f5fa9;
    --muted-grey: #8b8d92;
    --text-light: #e6e6e8;
    --divider: #5a5c61;
  }
  * { box-sizing: border-box; margin: 0; padding: 0; }
  html, body {
    width: 1200px; height: 864px; overflow: hidden;
    background: var(--backdrop);
    font-family: "Source Sans 3", sans-serif;
  }
  .sheet {
    width: 1200px; height: 864px;
    display: flex; flex-direction: column;
    align-items: center; justify-content: center; gap: 48px;
  }
  .card {
    width: 660px; height: 377px;
    background: var(--card);
    border-radius: 4px;
    box-shadow: 0 10px 30px rgba(0,0,0,.45);
    position: relative;
  }
  /* front */
  .card-front {
    display: flex; flex-direction: column;
    align-items: center; justify-content: center; gap: 34px;
  }
  .wordmark {
    display: flex; align-items: center; gap: 14px;
    color: var(--brand-blue);
    font-weight: 700; font-size: 46px; letter-spacing: 1px;
    text-transform: uppercase; white-space: nowrap;
  }
  .wordmark-square {
    width: 22px; height: 22px; background: var(--brand-blue);
  }
  .front-url {
    color: var(--muted-grey);
    font-size: 15px; letter-spacing: 5px; white-space: nowrap;
  }
  /* back */
  .card-back {
    display: flex; align-items: center;
    padding: 0 36px 0 44px;
  }
  .back-brand {
    width: 210px; flex: none;
    color: var(--brand-blue);
    font-weight: 700; font-size: 36px; line-height: 1.05;
    text-transform: uppercase; letter-spacing: 1px;
  }
  .back-divider {
    width: 1px; height: 190px; background: var(--divider);
    margin: 0 24px 0 6px; flex: none;
  }
  .contact {
    color: var(--text-light); font-size: 16px; line-height: 1.4;
    white-space: nowrap;
  }
  .contact-name {
    color: var(--brand-blue); font-weight: 600; font-size: 22px;
    text-transform: uppercase; line-height: 1.1;
  }
  .contact-role {
    color: var(--muted-grey); font-size: 15px;
    text-transform: uppercase; margin-bottom: 12px;
  }
  .contact-row { display: flex; align-items: center; gap: 8px; }
  .contact-row svg { width: 12px; height: 12px; flex: none; fill: var(--muted-grey); }
  .contact-address { margin-bottom: 2px; }
</style>
</head>
<body>
<main class="sheet">
  <section class="card card-front">
    <div class="wordmark"><span class="wordmark-square"></span>Dunmore Roofing</div>
    <p class="front-url">www.dunmoreroofing-example.com</p>
  </section>

  <section class="card card-back">
    <div class="back-brand">Dunmore<br>Roofing</div>
    <div class="back-divider"></div>
    <div class="contact">
      <p class="contact-name">Paul Dunmore</p>
      <p class="contact-role">Owner</p>
      <p class="contact-address">4172 Township road 43<br>Bramhollow, ON K9X4T2</p>
      <p class="contact-row">
        <svg viewBox="0 0 12 12" aria-hidden="true"><path d="M1 3c0-1 1-2 2-2h6c1 0 2 1 2 2v1H8V3H4v1H1zM2 5h8l1 6H1z"/></svg>
        613 555 0147
      </p>
      <p class="contact-row">
        <svg viewBox="0 0 12 12" aria-hidden="true"><path d="M0 2h12v8H0zM1 3v.4l5 3.2 5-3.2V3z"/></svg>
        paul@dunmoreroofing-example.com
      </p>
      <p class="contact-row">
        <svg viewBox="0 0 12 12" aria-hidden="true"><circle cx="6" cy="6" r="6"/></svg>
        www.dunmoreroofing-example.com
      </p>
    </div>
  </section>
</main>
</body>
</html>
```